real esate business card with company logo and name

we need a business card design for a real esate company

The company name is Walsh & Brand Pty Ltd, and we have our logo designed and will upload. We want classic or moden feel. Black or white background. looks more textured. Should include folowinginformations
Owen Walsh and Lucy Brand
Sales Agents & Onsite Manager
p: 07 5948 2063
F: 07 5948 2174
M:0431 857 219
3/42 Marlow Crescent, FERNLEA QLD 4213

We want this business card looks professonal. Thank you in advance.

Industry/Entity Type

Real Estate Agent

Contact Information for Business Card

Owen Walsh and Lucy Brand
Onsite Manager & Sales Agents
p: 07 5948 2063
M:0431 857 219

Font styles to use
Serif

Colors
000000
fbfbfb
333333
959595

Requirements
Must have
• company logo and name, black or white back ground

```html
<!DOCTYPE html>
<html lang="en">
<head>
<meta charset="utf-8">
<title>Walsh &amp; Brand Pty Ltd – Business Card</title>
<link rel="stylesheet" href="https://fonts.googleapis.com/css2?family=Tinos:wght@400&display=swap">
<style>
  :root {
    --ink: #000000;
    --paper: #fbfbfb;
    --charcoal: #333333;
    --steel: #959595;
    --backdrop: #e4e4e4;
  }
  * { margin: 0; padding: 0; box-sizing: border-box; }
  html, body {
    width: 1200px;
    height: 892px;
    overflow: hidden;
    background: var(--backdrop);
  }
  .business-card {
    position: absolute;
    left: 150px;
    top: 196px;
    width: 900px;
    height: 500px;
    overflow: hidden;
    box-shadow: 0 10px 30px rgba(0,0,0,0.25);
    font-family: "Tinos", "Times New Roman", serif;
    color: var(--paper);
  }
  .card-backdrop { position: absolute; inset: 0; }
  .company-mark {
    position: absolute;
    left: 232px;
    top: 62px;
    width: 330px;
    display: flex;
    flex-direction: column;
    align-items: center;
    gap: 18px;
  }
  .company-mark .mark-square {
    width: 120px;
    height: 120px;
    background: var(--steel);
  }
  .company-mark .company-name {
    font-size: 22px;
    letter-spacing: 1px;
    color: var(--steel);
    white-space: nowrap;
  }
  .people {
    position: absolute;
    left: 600px;
    top: 58px;
  }
  .person-name { font-size: 42px; line-height: 1.05; white-space: nowrap; }
  .person-role { font-size: 20px; line-height: 1.25; margin-bottom: 12px; }
  .contact-list {
    position: absolute;
    left: 460px;
    top: 306px;
    list-style: none;
    font-size: 25px;
    line-height: 1.15;
  }
  .contact-list li { display: flex; align-items: flex-start; gap: 14px; margin-bottom: 8px; }
  .contact-icon {
    flex: none;
    width: 22px;
    height: 22px;
    margin-top: 4px;
    background: var(--paper);
    border-radius: 3px;
    display: flex;
    align-items: center;
    justify-content: center;
  }
  .contact-icon svg { width: 16px; height: 16px; fill: var(--ink); }
</style>
</head>
<body>
  <div class="business-card">
    <svg class="card-backdrop" viewBox="0 0 900 500" width="900" height="500" aria-hidden="true">
      <rect class="side-panel" width="900" height="500" fill="#333333"/>
      <path class="curve-ribbon" d="M236 0 Q -20 240 62 500 L 96 500 Q 40 250 270 0 Z" fill="#fbfbfb"/>
      <path class="main-panel" d="M270 0 Q 40 250 96 500 L 900 500 L 900 0 Z" fill="#000000"/>
    </svg>

    <div class="company-mark">
      <span class="mark-square"></span>
      <span class="company-name">WALSH &amp; BRAND PTY LTD.</span>
    </div>

    <div class="people">
      <p class="person-name">Owen Walsh</p>
      <p class="person-role">Onsite Manager</p>
      <p class="person-name">Lucy Brand</p>
      <p class="person-role">Sales Agents</p>
    </div>

    <ul class="contact-list">
      <li>
        <span class="contact-icon"><svg viewBox="0 0 16 16"><path d="M3.5 1.5l2.5 0 1 3.5-1.6 1.2a8 8 0 0 0 4.4 4.4l1.2-1.6 3.5 1v2.5c0 .8-.7 1.5-1.5 1.5A11.5 11.5 0 0 1 2 3c0-.8.7-1.5 1.5-1.5z"/></svg></span>
        <span class="contact-text">07 5948 2063</span>
      </li>
      <li>
        <span class="contact-icon"><svg viewBox="0 0 16 16"><path d="M5 1h6a1 1 0 0 1 1 1v12a1 1 0 0 1-1 1H5a1 1 0 0 1-1-1V2a1 1 0 0 1 1-1zm0.6 2v8h4.8V3zM8 12.2a.8.8 0 1 0 0 1.6.8.8 0 0 0 0-1.6z"/></svg></span>
        <span class="contact-text">0431 857 219</span>
      </li>
      <li>
        <span class="contact-icon"><svg viewBox="0 0 16 16"><path d="M8 1a5 5 0 0 1 5 5c0 3.5-5 9-5 9S3 9.5 3 6a5 5 0 0 1 5-5zm0 3a2 2 0 1 0 0 4 2 2 0 0 0 0-4z"/></svg></span>
        <span class="contact-text">3/42 Marlow Crescent,<br>FERNLEA QLD 4213</span>
      </li>
    </ul>
  </div>
</body>
</html>
```